Zielgruppe
Die Velorin Akademie bietet Kurse, Seminare & Coachings im Bereich der Kommunikation / Persönlichkeitsentwicklung an.
Folgendes Angebot besteht zur Zeit:
Seminare:
- 'Erste Schritte im Dialog', eine Einführung in die Kommunikation.
- 'Heitere Töchter, ruhige Väter' zum Thema Erziehung.
- 'Reifen mit Gelassenheit', zum Thema Älter werden und den Umgang damit.
Kurse:
- 'Gewaltfreie Kommunikation', Übungsgruppe
Coaching:
- Einzelsitzungen mit Hypnose
Ps: im Anhang unter 'Angabot_Vorlage.pdf' finden Sie mehr Infos zu den einezlenen Angebote.
Aufgabenstellung
Bitte berücksichtigen Sie, dass bereits ein Logo besteht (siehe Anhang).
Vom gesamteindruck her sollte die Website aufgeräumt, übersichtlich, harmonisch, freundlich & frisch wirken.
Es wäre super, wenn die Website authentisch wirkt (und weniger '0815 Business Website').
Bitte bedenken Sie, dass die Website sich an Private richtet, die sich nach einem 'strahlenderen & unbeschwerterem Lebene sehnen'.
Wir haben bereits viele Persönlichkeiten stärken können und möchten dies auch witerhin mit viel Herzblut machen.

```html
<!DOCTYPE html>
<html lang="de">
<head>
<meta charset="utf-8">
<title>Velorin Akademie</title>
<link rel="stylesheet" href="https://fonts.googleapis.com/css2?family=Abel&family=Roboto:wght@400;500&family=Roboto+Condensed:ital,wght@0,300;0,400;1,300&display=swap">
<style>
:root{
  --teal:#2dd4ae;
  --ink:#333;
  --muted:#8a8a8a;
  --light:#f0f0f0;
  --white:#fff;
}
*{box-sizing:border-box;margin:0;padding:0}
html,body{width:670px;height:1200px;overflow:hidden;background:var(--white)}
body{position:relative;font-family:"Roboto Condensed",sans-serif;color:var(--ink)}
.abs{position:absolute}
.heading{font-family:"Abel",sans-serif;font-weight:400}

/* top bar */
.topbar{left:0;top:0;width:670px;height:23px;background:var(--teal)}
.topbar-btn{left:140px;top:4px;width:140px;height:15px;background:var(--white);color:var(--teal);font:500 5.6px/15px "Roboto",sans-serif;text-align:center;border-radius:1px}
.social-sq{width:11px;height:11px;background:var(--white);border-radius:1px}

/* header */
.brand{left:0;top:58px;width:670px;text-align:center;font-family:"Abel",sans-serif;font-weight:400;font-size:20px;line-height:24px;color:var(--ink)}
.nav-line{left:136px;top:102px;width:398px;border-top:1px dotted #c8c8c8}
.nav-bottom{left:0;top:121px;width:670px;border-top:1px solid #e6e6e6}
.nav-item{top:107px;font:400 5.4px/10px "Roboto",sans-serif;color:var(--ink);text-align:center}
.nav-active{left:233px;top:102px;width:44px;height:19px;border-top:1px solid var(--teal);border-bottom:1.5px solid var(--teal)}

/* hero */
.hero{left:126px;top:122px;width:418px;height:210px;background:linear-gradient(100deg,#2f3d26 0%,#40502f 35%,#6b6a54 55%,#b49579 70%,#556140 88%,#2d3a24 100%)}
.hero-title{left:161px;top:169px;width:170px;font-size:17.5px;line-height:17.5px;color:var(--teal)}
.hero-text{left:161px;top:230px;width:180px;font-size:8.4px;line-height:12.2px;color:var(--white);font-weight:300}
.hero-form{left:161px;top:273px;width:348px;height:39px;background:rgba(255,255,255,.55)}
.field{height:18px;background:var(--white);font:400 5.6px/18px Georgia,serif;color:#9a9a9a;padding-left:6px}
.hero-btn{left:368px;top:286px;width:93px;height:15px;background:var(--teal);color:var(--white);font:500 6.2px/15px "Roboto",sans-serif;letter-spacing:.6px;text-align:center}

/* intro */
.intro{left:126px;top:332px;width:418px;height:168px;background:var(--light)}
.intro-title{left:161px;top:346px;font-size:10.5px;color:var(--ink)}
.intro-text{left:161px;top:365px;width:345px;font-size:5.2px;line-height:9.8px;color:#666;font-weight:300}
.feature-icon{top:408px;width:14px;height:14px}
.feature-title{top:408px;font-family:"Abel",sans-serif;font-size:6.4px;line-height:8.6px;color:var(--ink)}
.feature-sub{font-size:4.8px;line-height:9.4px;color:var(--muted);font-weight:300}
.intro-btn{left:306px;top:451px;width:57px;height:14px;background:var(--teal);color:var(--white);font:500 5px/14px "Roboto",sans-serif;text-align:center;border-radius:1px}

/* about */
.about{left:126px;top:500px;width:418px;height:195px;background:var(--teal)}
.about-title{left:161px;top:533px;font-size:10.5px;color:var(--ink)}
.about-text{left:161px;top:556px;width:168px;font-size:5.4px;line-height:10.5px;color:#1f5e50;font-weight:300}
.about-photo{left:344px;top:541px;width:165px;height:112px;border:2.5px solid var(--white);background:linear-gradient(90deg,#eee9e0 0%,#e6e1d8 45%,#8b6f52 62%,#5b4330 100%)}

/* testimonials */
.voices{left:126px;top:695px;width:418px;height:225px;background:linear-gradient(180deg,#4b5567 0%,#6d7684 40%,#5a6270 70%,#3f4656 100%)}
.voices-title{left:126px;top:712px;width:418px;text-align:center;font-size:10.5px;color:var(--teal)}
.quote{width:130px;font-size:5.3px;line-height:10.4px;color:var(--white);font-style:italic;font-weight:300}
.avatar{width:29px;height:29px;border-radius:50%;border:1.5px solid #d8d8d8;background:linear-gradient(160deg,#c9b3a0,#6b5a4d)}
.voice-name{font-size:8px;color:var(--teal)}

/* call to action */
.cta{left:126px;top:920px;width:418px;height:103px;background:var(--teal)}
.cta-text{left:161px;top:936px;width:170px;font-size:13.2px;line-height:13.7px;color:var(--white)}
.cta-btn{left:335px;top:958px;width:174px;height:26px;background:var(--white);color:var(--teal);font:500 6.2px/7px "Roboto",sans-serif;letter-spacing:1.2px;text-align:center;padding-top:6px}

/* footer */
.footer-line{left:0;top:1039px;width:670px;border-top:1px solid var(--teal)}
.footer-brand{left:140px;top:1080px;font-family:"Abel",sans-serif;font-weight:400;font-size:12px;line-height:14px;color:var(--ink)}
.footer-text{left:140px;top:1101px;width:95px;font:400 4.9px/8.6px "Roboto",sans-serif;color:var(--muted)}
.footer-sq{top:1150px;width:12px;height:12px;background:var(--teal)}
.footer-title{top:1062px;font:400 6.2px/8px "Roboto",sans-serif;color:var(--teal)}
.footer-link{left:285px;font:400 4.6px/6px "Roboto",sans-serif;color:var(--ink)}
.footer-link::before{content:"";display:inline-block;width:0;height:0;border-left:2px solid #bbb;border-top:1.5px solid transparent;border-bottom:1.5px solid transparent;margin-right:5px;vertical-align:1px}
.footer-field{left:405px;width:125px;height:14px;border:1px solid #cfcfcf;font:400 4.4px/12px "Roboto",sans-serif;color:#aaa;padding-left:5px}
.footer-btn{left:405px;top:1111px;width:125px;height:14px;background:var(--teal);color:var(--white);font:500 4.5px/14px "Roboto",sans-serif;letter-spacing:1.8px;text-align:center}
.copyright-bar{left:0;top:1183px;width:670px;height:17px;background:#f2f2f2}
.copyright{left:140px;top:1189px;font:400 4.2px/5px "Roboto",sans-serif;color:var(--muted)}
</style>
</head>
<body>

<!-- top bar -->
<div class="abs topbar"></div>
<div class="abs topbar-btn">KOSTENLOSES ERSTGESPRÄCH VEREINBAREN</div>
<div class="abs social-sq" style="left:506px;top:6px" aria-hidden="true"></div>
<div class="abs social-sq" style="left:519px;top:6px" aria-hidden="true"></div>

<!-- header -->
<div class="abs brand">Velorin Akademie</div>
<div class="abs nav-line"></div>
<div class="abs nav-active"></div>
<div class="abs nav-item" style="left:233px;width:44px">HOME</div>
<div class="abs nav-item" style="left:284px;width:40px">ANGEBOTE</div>
<div class="abs nav-item" style="left:338px;width:40px">KONTAKT</div>
<div class="abs nav-item" style="left:390px;width:40px">ÜBER UNS</div>
<div class="abs nav-bottom"></div>

<!-- hero -->
<div class="abs hero" role="img" aria-label="Foto: Frau mit geschlossenen Augen im Grünen vor blühenden Sträuchern"></div>
<h1 class="abs heading hero-title">Lorem ipsum dolor sit amet, consetetur sadipscing elitr!</h1>
<p class="abs hero-text">Lorem ipsum dolor sit amet, consetetur sadipscing elitr, sed diam nonumy eirmod tempor invidunt ut labore et dolore magna.</p>
<div class="abs hero-form"></div>
<div class="abs field" style="left:192px;top:283px;width:77px">Name</div>
<div class="abs field" style="left:272px;top:283px;width:77px">Email</div>
<div class="abs hero-btn">NEWSLETTER ANMELDEN</div>

<!-- intro -->
<div class="abs intro"></div>
<h2 class="abs heading intro-title">Introtext</h2>
<p class="abs intro-text">Lorem ipsum dolor sit amet, consectetur adipiscing elit. Ut elit tellus, luctus nec ullamcorper mattis, pulvinar dapibus leo. Lorem ipsum dolor sit amet, consectetur adipiscing elit. Ut elit tellus, luctus nec ullamcorper mattis, pulvinar dapibus leo. Lorem ipsum dolor sit amet, consectetur adipiscing elit. Ut elit tellus, luctus nec ullamcorper mattis, pulvinar dapibus leo.</p>

<svg class="abs feature-icon" style="left:160px" viewBox="0 0 14 14" aria-hidden="true"><ellipse cx="7" cy="5" rx="6.5" ry="4" fill="#2dd4ae"/><circle cx="3" cy="10" r="1.3" fill="#2dd4ae"/><circle cx="1.5" cy="12.5" r=".8" fill="#2dd4ae"/></svg>
<div class="abs feature-title" style="left:181px;width:60px">Erste Schritte im Dialog</div>
<div class="abs feature-sub" style="left:181px;top:432px;width:60px">Eine Einführung in die Kommunikation</div>

<svg class="abs feature-icon" style="left:251px" viewBox="0 0 14 14" aria-hidden="true"><circle cx="7" cy="2.2" r="2" fill="#2dd4ae"/><rect x="4.8" y="5" width="4.4" height="6" rx="1.5" fill="#2dd4ae"/><path d="M3 13.5h8" stroke="#2dd4ae" stroke-width="1"/></svg>
<div class="abs feature-title" style="left:271px;width:60px">Kinder &amp; Eltern</div>
<div class="abs feature-sub" style="left:271px;top:423px;width:60px">Einführung in das Thema Erziehung</div>

<svg class="abs feature-icon" style="left:338px" viewBox="0 0 14 14" aria-hidden="true"><path d="M4 6a4 4 0 1 1 7 2.5c-1 1-2 1.5-2 3a2 2 0 0 1-3.5 1.3" fill="none" stroke="#2dd4ae" stroke-width="1.2"/><path d="M6 6a2 2 0 1 1 3 1.5" fill="none" stroke="#2dd4ae" stroke-width="1"/></svg>
<div class="abs feature-title" style="left:358px;width:60px">Realität</div>
<div class="abs feature-sub" style="left:358px;top:423px;width:60px">Älter werden und damit umgehen können</div>

<svg class="abs feature-icon" style="left:425px" viewBox="0 0 14 14" aria-hidden="true"><rect x="2.5" y="2" width="9" height="6" rx="1.5" fill="#2dd4ae"/><rect x=".5" y="5" width="13" height="5" rx="1.5" fill="#2dd4ae"/><path d="M3 10v2.5M11 10v2.5" stroke="#2dd4ae" stroke-width="1"/></svg>
<div class="abs feature-title" style="left:445px;width:60px">Hypnose</div>
<div class="abs feature-sub" style="left:445px;top:423px;width:60px">Lorem Ipsum</div>

<div class="abs intro-btn">Unsere Angebote</div>

<!-- about -->
<div class="abs about"></div>
<h2 class="abs heading about-title">Über uns</h2>
<p class="abs about-text">Lorem ipsum dolor sit amet, consetetur sadipscing elitr, sed diam nonumy eirmod tempor invidunt ut labore et dolore magna aliquyam erat, sed diam voluptua. At vero eos et accusam et justo duo dolores et ea rebum. Stet clita kasd gubergren, no sea takimata sanctus est Lorem ipsum dolor sit amet. Lorem ipsum dolor sit amet, consetetur sadipscing elitr, sed diam nonumy eirmod tempor invidunt ut labore et dolore magna aliquyam erat, sed diam voluptua. At vero eos et accusam et justo duo dolores et ea rebum. Stet clita kasd gubergren, no sea takimata sanctus est Lorem ipsum dolor sit amet.</p>
<div class="abs about-photo" role="img" aria-label="Foto: heller Praxisraum mit blauem Sofa, Sesseln und Bücherregal"></div>

<!-- testimonials -->
<div class="abs voices" role="img" aria-label="Hintergrundfoto: bewölkter Himmel über Bergen mit Lichtstrahlen"></div>
<h2 class="abs heading voices-title">Was unsere Kunden sagen</h2>

<p class="abs quote" style="left:178px;top:748px">Lorem ipsum dolor sit amet, consetetur sadipscing elitr, sed diam nonumy eirmod tempor invidunt ut labore et dolore magna aliquyam erat</p>
<div class="abs avatar" style="left:178px;top:786px" role="img" aria-label="Porträtfoto der Kundin"></div>
<div class="abs heading voice-name" style="left:212px;top:795px">Anna B.</div>

<p class="abs quote" style="left:366px;top:748px">Lorem ipsum dolor sit amet, consetetur sadipscing elitr, sed diam nonumy eirmod tempor invidunt ut labore et dolore magna aliquyam erat</p>
<div class="abs avatar" style="left:367px;top:786px" role="img" aria-label="Porträtfoto des Kunden"></div>
<div class="abs heading voice-name" style="left:401px;top:795px">David A.</div>

<p class="abs quote" style="left:178px;top:834px">Lorem ipsum dolor sit amet, consetetur sadipscing elitr, sed diam nonumy eirmod tempor invidunt ut labore et dolore magna aliquyam erat</p>
<div class="abs avatar" style="left:178px;top:873px" role="img" aria-label="Porträtfoto des Kunden"></div>
<div class="abs heading voice-name" style="left:212px;top:882px">Leo H.</div>

<!-- call to action -->
<div class="abs cta"></div>
<p class="abs heading cta-text">Lorem ipsum dolor sit amet, consetetur sadipscing elitr, sed diam nonumy eirmod tempor invidunt ut labore et dolore magna aliquyam erat</p>
<div class="abs cta-btn">KOSTENLOSES ERSTGESPRÄCH<br>VEREINBAREN</div>

<!-- footer -->
<div class="abs footer-line"></div>
<div class="abs footer-brand">Velorin Akademie</div>
<p class="abs footer-text">Lorem ipsum dolor sit amet, consectetur adipiscing elit. Ut elit tellus, luctus nec ullamcorper mattis, pulvinar dapibus leo.</p>
<div class="abs footer-sq" style="left:140px" aria-hidden="true"></div>
<div class="abs footer-sq" style="left:153px" aria-hidden="true"></div>

<div class="abs footer-title" style="left:285px">Navigation</div>
<div class="abs footer-link" style="top:1087px">Home</div>
<div class="abs footer-link" style="top:1100px">Angebote</div>
<div class="abs footer-link" style="top:1113px">Kontakt</div>
<div class="abs footer-link" style="top:1126px">Über uns</div>

<div class="abs footer-title" style="left:405px">Newsletter</div>
<div class="abs footer-field" style="top:1075px">Name</div>
<div class="abs footer-field" style="top:1093px">E-Mail</div>
<div class="abs footer-btn">NEWSLETTER ANMELDEN</div>

<div class="abs copyright-bar"></div>
<div class="abs copyright">© 2019 Velorin Akademie</div>

</body>
</html>
```